Coastline Premier Retreats Business Card Design

Design a business card for Coastline Premier Retreats. Look at the website for colors and reference. Card should have logo, name, title, office number, mobile number, email, URL and a tagline like, "Luxury Hotel & Resort Email Marketing" (This might change).

https://www.coastlinepremierretreats.example

The rest I will leave up to your imagination.

Contact Information for Business Card

Logo, name, title, office number, mobile number, email, URL and a tagline like, "Luxury Hotel & Resort Email Marketing" (This might change).

```html
<!DOCTYPE html>
<html lang="en">
<head>
<meta charset="utf-8">
<title>Coastline Premier Retreats – Business Card</title>
<link rel="stylesheet" href="https://fonts.googleapis.com/css2?family=Montserrat:wght@400;500;600;700;800&display=swap">
<style>
  :root {
    --orange: #f07423;
    --orange-light: #f6a676;
    --ink: #231f20;
    --pill: #2b2b2d;
    --paper: #f1f1f1;
    --paper-shade: #e6e6e6;
    --bg: #dcdcdc;
    --white: #ffffff;
  }
  * { box-sizing: border-box; margin: 0; padding: 0; }
  html, body { width: 1200px; height: 1200px; overflow: hidden; }
  body {
    background: var(--bg);
    font-family: "Montserrat", Arial, sans-serif;
    display: flex;
    flex-direction: column;
    align-items: center;
    justify-content: center;
    gap: 56px;
  }
  .card {
    position: relative;
    width: 900px;
    height: 514px;
    border-radius: 28px;
    overflow: hidden;
    box-shadow: 0 8px 22px rgba(0,0,0,0.18);
  }
  /* Front */
  .card--front {
    background: linear-gradient(90deg, var(--orange-light) 0%, var(--orange) 62%, var(--orange) 100%);
  }
  .front__brand {
    position: absolute;
    left: 0; right: 0; top: 170px;
    text-align: center;
    color: var(--white);
    font-weight: 800;
    font-size: 50px;
    letter-spacing: 1px;
    text-transform: uppercase;
    line-height: 1.1;
  }
  .front__rule {
    position: absolute;
    top: 382px;
    left: 0; right: 0;
    height: 2px;
    background: var(--white);
  }
  .front__tagline {
    position: absolute;
    top: 354px;
    left: 50%;
    transform: translateX(-50%);
    background: linear-gradient(90deg, var(--pill), #0c0c0c);
    color: var(--white);
    font-weight: 500;
    font-size: 20px;
    padding: 16px 40px;
    border-radius: 30px;
    white-space: nowrap;
  }
  /* Back */
  .card--back {
    background: linear-gradient(135deg, var(--paper) 0%, var(--paper-shade) 100%);
  }
  .back__brand {
    position: absolute;
    top: 50px;
    right: 48px;
    color: var(--ink);
    font-weight: 800;
    font-size: 28px;
    text-transform: uppercase;
    letter-spacing: 0.5px;
  }
  .back__top-rule {
    position: absolute;
    top: 214px;
    right: 0;
    width: 72%;
    height: 2px;
    background: var(--orange);
  }
  .person {
    position: absolute;
    left: 60px;
    top: 268px;
  }
  .person__name {
    color: var(--orange);
    font-weight: 700;
    font-size: 36px;
  }
  .person__title {
    color: var(--ink);
    font-size: 20px;
    font-weight: 500;
    margin-top: 4px;
  }
  .back__rule {
    position: absolute;
    left: 60px; right: 0;
    top: 360px;
    height: 2px;
    background: var(--orange);
  }
  .contact {
    position: absolute;
    left: 60px;
    right: 30px;
    top: 376px;
    color: var(--ink);
    font-size: 19px;
    font-weight: 500;
    line-height: 1.5;
  }
  .contact__region { color: var(--orange); }
  .contact__row { display: flex; align-items: center; gap: 8px; white-space: nowrap; }
  .contact__row .icon { width: 18px; height: 18px; flex: none; }
  .contact__gap { width: 14px; }
</style>
</head>
<body>
  <section class="card card--front">
    <div class="front__brand">Coastline Premier Retreats</div>
    <div class="front__rule"></div>
    <div class="front__tagline">Luxury Hotel &amp; Resort Email Marketing</div>
  </section>

  <section class="card card--back">
    <div class="back__brand">Coastline Premier Retreats</div>
    <div class="back__top-rule"></div>
    <div class="person">
      <div class="person__name">Daniel Morrow</div>
      <div class="person__title">Founder &amp; Director</div>
    </div>
    <div class="back__rule"></div>
    <div class="contact">
      <div class="contact__row"><span class="contact__region">North America,</span> 4870 Harbor View Road Seaport Bay 20417</div>
      <div class="contact__row">
        <svg class="icon" viewBox="0 0 24 24" aria-hidden="true"><path fill="#f07423" d="M6.6 10.8a15 15 0 0 0 6.6 6.6l2.2-2.2c.3-.3.7-.4 1-.2 1.1.4 2.3.6 3.6.6.6 0 1 .4 1 1V20c0 .6-.4 1-1 1A17 17 0 0 1 3 4c0-.6.4-1 1-1h3.5c.6 0 1 .4 1 1 0 1.3.2 2.5.6 3.6.1.3 0 .7-.2 1z"/></svg>
        555.014.2200
        <span class="contact__gap"></span>
        <svg class="icon" viewBox="0 0 24 24" aria-hidden="true"><rect x="6" y="2" width="12" height="20" rx="2" fill="none" stroke="#f07423" stroke-width="2.2"/><circle cx="12" cy="18" r="1.3" fill="#f07423"/></svg>
        555-019-3381
        <span class="contact__gap"></span>
        <svg class="icon" viewBox="0 0 24 24" aria-hidden="true"><rect x="2" y="5" width="20" height="14" rx="1.5" fill="#f07423"/><path d="M3 6l9 7 9-7" fill="none" stroke="#fff" stroke-width="1.8"/></svg>
        info@coastlinepremierretreats.example
      </div>
      <div class="contact__row">
        <svg class="icon" viewBox="0 0 24 24" aria-hidden="true"><circle cx="12" cy="12" r="10" fill="#f07423"/><path d="M2 12h20M12 2c3 3 3 17 0 20M12 2c-3 3-3 17 0 20" fill="none" stroke="#fff" stroke-width="1.4"/></svg>
        www.coastlinepremierretreats.example
      </div>
    </div>
  </section>
</body>
</html>
```